Recruitment Site Design

We need a design for the login page, about page, and inner pages of a recruitment site for an oil and gas company. Design should be modern, sleek, professional and colors can be blue, green, white, orange or any other recommended colors.

Please also take into consideration that once the users login, they will need to access a form to fill in their information.

** UPDATE: Kindly provide a design for the inner information page consistent with the outer design. Attached is a picture of the basic structure. ***
Updates

Please provide a design for inner pages as shown in the design brief consistent with the registration page provided. 

Reason: We're extending it to get more inside pages.

Target Market(s)

Professionals looking for a career in the oil and gas industry in the Middle East.

Industry/Entity Type

Oil And Gas

Requirements
Must have
• Sleek design

```html
<!DOCTYPE html>
<html lang="en">
<head>
<meta charset="utf-8">
<title>Wellvane — Oil &amp; Gas Careers</title>
<link rel="stylesheet" href="https://fonts.googleapis.com/css2?family=Source+Sans+3:wght@400;600;700&family=Arimo:wght@400;700&display=swap">
<style>
:root{
  --navy:#272c38;
  --navy-deep:#1f232d;
  --teal:#5fb8c9;
  --rust:#c0391d;
  --rust-dark:#a8301a;
  --rust-light:#cf4a28;
  --text:#333;
  --muted:#7d828c;
  --line:#d9d9d9;
  --panel:#ececec;
  --white:#fff;
}
*{box-sizing:border-box;margin:0;padding:0}
html,body{width:1136px;height:1200px;overflow:hidden;background:var(--white)}
body{font-family:"Arimo",Arial,sans-serif;color:var(--text);position:relative}
.header{position:absolute;top:0;left:0;width:1136px;height:106px;background:var(--navy)}
.brand{position:absolute;left:176px;top:20px}
.brand-name{font-family:"Source Sans 3",sans-serif;font-weight:400;font-size:44px;line-height:44px;color:var(--teal);letter-spacing:1px}
.brand-slogan{font-size:11.5px;color:#5c6574;margin-top:1px}
.account{position:absolute;right:173px;top:48px;font-size:10px;color:#7b8290;letter-spacing:.3px}
.account span{margin:0 14px}
.nav{position:absolute;top:106px;left:0;width:1136px;height:65px;background:linear-gradient(#cc4524,#b3321a);display:flex;padding-left:154px}
.nav a{font-family:"Source Sans 3",sans-serif;font-size:12.5px;color:#fbe7df;text-decoration:none;letter-spacing:.4px;height:65px;line-height:65px;text-align:center;border-right:1px solid #d86a4c}
.hero{position:absolute;top:171px;left:0;width:1136px;height:346px;background:radial-gradient(ellipse at 50% 75%,#6c7584 0%,#3a404c 40%,#1d212a 80%)}
.hero-title{position:absolute;top:37px;width:100%;text-align:center;font-family:"Source Sans 3",sans-serif;color:#f2f4f7}
.hero-title .l1{font-size:28px;font-weight:400;letter-spacing:.5px}
.hero-title .l2{font-size:32px;font-weight:700;color:#d6dae0;margin-top:6px}
.hero-text{position:absolute;top:128px;left:322px;width:492px;height:64px;background:rgba(40,44,54,.55);color:#f0f0f0;font-size:9.8px;line-height:16px;text-align:center;padding:4px 14px}
.section-title{font-family:"Source Sans 3",sans-serif;font-weight:600;color:var(--rust)}
.sponsor-title{position:absolute;top:540px;width:100%;text-align:center;font-size:15px}
.sponsors{position:absolute;top:572px;left:168px;width:800px;height:90px;border-top:1px solid var(--line);border-bottom:1px solid var(--line);display:flex;align-items:center;justify-content:space-around;padding:0 30px}
.sponsor-badge{background:#c9cbcf;border-radius:3px}
.welcome{position:absolute;top:684px;left:168px;width:470px}
.welcome h2{font-size:21px;margin-bottom:20px}
.welcome .lead{font-size:9.6px;font-weight:700;line-height:14.4px;margin-bottom:14px}
.welcome p{font-size:9.6px;line-height:14.4px}
.search{position:absolute;top:688px;left:680px;width:288px;height:219px;background:var(--panel);border-radius:10px;padding:20px 18px}
.search h3{font-family:"Source Sans 3",sans-serif;font-weight:600;font-size:15.5px;color:#333;margin-bottom:6px}
.search .hint{font-size:9.3px;color:var(--muted);line-height:14.4px}
.field{display:block;width:246px;height:30px;background:var(--white);border:1px solid #d3d3d3;margin-top:14px;font-size:9.6px;color:#888;padding:0 9px;line-height:28px}
.field+.field{margin-top:12px}
.btn{display:inline-block;margin-top:8px;width:101px;height:38px;background:linear-gradient(var(--rust-light),var(--rust-dark));color:var(--white);font-family:"Source Sans 3",sans-serif;font-size:15px;line-height:38px;text-align:center}
.testimonials-title{position:absolute;top:938px;left:168px;font-size:21px}
.quotes{position:absolute;top:976px;left:168px;width:800px;display:flex;gap:30px}
.quote{width:250px;position:relative;padding-left:23px}
.quote .mark{position:absolute;left:0;top:-6px;font-family:Georgia,serif;font-size:30px;color:#bbb}
.quote p{font-size:9.6px;line-height:16.2px}
.author{display:flex;align-items:center;margin-top:16px;font-size:9.6px;line-height:15.6px}
.author svg{margin-right:8px}
.footer{position:absolute;top:1138px;left:0;width:1136px;height:62px;background:var(--navy)}
.footer-links{position:absolute;left:175px;top:16px;font-size:9.6px;color:#6d7482}
.footer-copy{position:absolute;left:175px;top:35px;font-size:9.6px;color:#5e6573}
.footer-copy b{font-weight:400;color:var(--teal)}
.follow{position:absolute;right:164px;top:18px;display:flex;align-items:center;gap:5px;font-size:9.6px;color:#6d7482}
.follow span{margin-right:12px}
.social{width:24px;height:24px;background:#6d93ad;border-radius:3px}
</style>
</head>
<body>
<header class="header">
  <div class="brand">
    <div class="brand-name">Wellvane</div>
    <div class="brand-slogan">slogan comes here</div>
  </div>
  <div class="account">LOGIN<span>|</span>REGISTER HERE</div>
</header>

<nav class="nav">
  <a style="width:108px">ABOUT US</a>
  <a style="width:95px">JOBS</a>
  <a style="width:77px">BLOG</a>
  <a style="width:119px">FIND NOW</a>
  <a style="width:103px">LOCATION</a>
  <a style="width:115px">CONTACTS</a>
</nav>

<section class="hero" role="img" aria-label="Monochrome photograph of oil storage tanks with ladders at dusk">
  <div class="hero-title">
    <div class="l1">JOBSEEKERS IN OIL &amp; GAS INDUSTRY</div>
    <div class="l2">FOR MIDDLE EAST JOBS.</div>
  </div>
  <div class="hero-text">Lorem ipsum dolor sit amet, consectetur adipiscing elit. Curabitur a risus purus, in sodales leo. Vestibulum ornare, massa in placerat porttitor, lacus risus scelerisque erat, eget tempor ipsum nunc eu nibh. Nulla lorem erat, ornare a placerat id, dapibus eget metus.</div>
</section>

<h2 class="section-title sponsor-title">OUR SPONSOR</h2>
<div class="sponsors">
  <div class="sponsor-badge" style="width:38px;height:48px"></div>
  <div class="sponsor-badge" style="width:100px;height:28px"></div>
  <div class="sponsor-badge" style="width:80px;height:30px"></div>
  <div class="sponsor-badge" style="width:80px;height:28px"></div>
  <div class="sponsor-badge" style="width:82px;height:22px;background:#444"></div>
  <div class="sponsor-badge" style="width:28px;height:16px"></div>
  <div class="sponsor-badge" style="width:80px;height:40px"></div>
  <div class="sponsor-badge" style="width:72px;height:34px"></div>
</div>

<section class="welcome">
  <h2 class="section-title">WELCOME TO OUR Wellvane</h2>
  <p class="lead">Nunc orci ligula, feugiat sed congue id, sagittis sed arcu. Etiam ultrices commodo magna, non semper lorem vulputate quis. Nulla facilisi. Nunc at aliquam felis.</p>
  <p>Curabitur condimentum, nisi id cursus tristique, purus purus tincidunt nisl, non rhoncus tortor erat nec nisl. Vestibulum a risus lectus, vitae ultricies turpis. Quisque diam purus, tincidunt eget ultricies et, fermentum et massa. Sed blandit neque odio. Vivamus tincidunt lectus sed elit consectetur faucibus. Mauris vitae nulla eu lectus elementum porttitor at eu nulla. Donec tempus, nisi et ornare sagittis, velit turpis adipiscing nulla, ac scelerisque massa mauris sit amet lacus. Aliquam sit amet vestibulum eros. Vivamus volutpat aliquam est in rhoncus. Phasellus dui odio, commodo sed suscipit non, porta a odio. Praesent adipiscing aliquet tincidunt. Morbi ullamcorper leo quis mi scelerisque tempor. Praesent velit massa, dignissim ut sollicitudin eu, dapibus a augue. Morbi ultricies tincidunt velit, eu rhoncus libero aliquam quis. Donec nisl urna, egestas ac ultrices ac, cursus in orci.</p>
</section>

<aside class="search">
  <h3>QUICK SEARCH</h3>
  <div class="hint">Enter Keyword(s):<br>(i.e. job title, company name, etc.) :</div>
  <div class="field"></div>
  <div class="field">Enter city and state</div>
  <div class="btn">SEARCH</div>
</aside>

<h2 class="section-title testimonials-title">TESTIMONIALS</h2>
<section class="quotes">
  <div class="quote">
    <span class="mark">“</span>
    <p>Nunc convallis odio dignissim enim dictum fringilla. Nam faucibus pharetra lectus, eu faucibus ligula posuere in. Nulla facilisi. Quisque pellentesque velit eget neque viverra non iaculis ante mollis.</p>
    <div class="author"><svg width="32" height="34" viewBox="0 0 32 34"><circle cx="16" cy="10" r="8" fill="#c4c4c4"/><path d="M0 34c0-10 7-14 16-14s16 4 16 14z" fill="#c4c4c4"/></svg><div>Dana Harlow,<br>Northwind, UK</div></div>
  </div>
  <div class="quote">
    <span class="mark">“</span>
    <p>Etiam mattis erat et ipsum tincidunt a mollis sapien aliquet. Curabitur in nisl justo, vitae laoreet augue. Morbi molestie dolor nulla. Nulla congue pretium erat sed posuere. Integer vel pulvinar quam.</p>
    <div class="author"><svg width="32" height="34" viewBox="0 0 32 34"><circle cx="16" cy="10" r="8" fill="#c4c4c4"/><path d="M0 34c0-10 7-14 16-14s16 4 16 14z" fill="#c4c4c4"/></svg><div>Dana Harlow,<br>Northwind, UK</div></div>
  </div>
  <div class="quote">
    <span class="mark">“</span>
    <p>Etiam at ipsum lectus, bibendum venenatis quam. Nulla ligula diam, eleifend ut pharetra in, ultricies convallis risus. Morbi vel suscipit tortor. Lorem ipsum dolor sit amet, consectetur adipiscing elit.</p>
    <div class="author"><svg width="32" height="34" viewBox="0 0 32 34"><circle cx="16" cy="10" r="8" fill="#c4c4c4"/><path d="M0 34c0-10 7-14 16-14s16 4 16 14z" fill="#c4c4c4"/></svg><div>Dana Harlow,<br>Northwind, UK</div></div>
  </div>
</section>

<footer class="footer">
  <div class="footer-links">Home | About Us | Jobs | Blog | Find Now | Location | Contacts</div>
  <div class="footer-copy">Copyright 2012 © <b>Wellvane</b>. All Rights Reserved.</div>
  <div class="follow"><span>Follow us:</span><div class="social"></div><div class="social"></div><div class="social"></div></div>
</footer>
</body>
</html>
```